Northline Claim Advocates Business card

We need to get business card Design for our Company we are Public Adjusters in Chicago Illinois - i like to see good combination and elements from my Company Logo. as well To be an two side design
Updates

Target Market(s)

Home /Business owner Property Managers

Industry/Entity Type

Business

Contact Information for Business Card

to show the Element of our logo i will Like 3D

Font styles to use
Sans Serif

Requirements
Must have
• Logo and Element of the Logo in 3D
Nice to have
• Logo That we Provide 3D Same Colors or open for suggestions
Should not have
• unleare view -

```html
<!DOCTYPE html>
<html lang="en">
<head>
<meta charset="utf-8">
<title>Northline Claim Advocates — Business Card</title>
<link href="https://fonts.googleapis.com/css2?family=Open+Sans:wght@400;600;700&display=swap" rel="stylesheet">
<style>
  :root {
    --page-bg: #e9e6e2;
    --card-white: #ffffff;
    --brand-blue: #1a2fb0;
    --brand-red: #d1382c;
    --text-grey: #4a4a4a;
    --divider: #d8d8d8;
    --navy-deep: #0d0f55;
    --royal: #1447c9;
    --band-silver: #dcdcdc;
  }
  * { margin: 0; padding: 0; box-sizing: border-box; }
  html, body { width: 1200px; height: 987px; overflow: hidden; }
  body {
    background: var(--page-bg);
    font-family: "Open Sans", sans-serif;
    position: relative;
  }
  .card {
    position: absolute;
    left: 293px;
    width: 615px;
    height: 352px;
    box-shadow: 0 3px 10px rgba(0,0,0,0.25);
    overflow: hidden;
  }
  .card--front { top: 130px; background: var(--card-white); }
  .card--back {
    top: 505px;
    background: radial-gradient(ellipse at 50% 45%, #1f6ae6 0%, var(--royal) 30%, #10229a 65%, var(--navy-deep) 100%);
  }

  .brand-lockup {
    position: absolute;
    left: 30px;
    width: 260px;
    top: 88px;
    text-align: center;
    color: var(--brand-blue);
    font-weight: 700;
  }
  .brand-lockup__mark {
    width: 66px; height: 66px;
    border-radius: 50%;
    background: var(--brand-blue);
    margin: 0 auto 62px;
  }
  .brand-lockup__name { font-size: 19px; line-height: 1.25; white-space: nowrap; }

  .front-divider {
    position: absolute;
    left: 320px; top: 52px;
    width: 1px; height: 234px;
    background: var(--divider);
  }
  .contact {
    position: absolute;
    left: 355px; top: 52px;
    color: var(--text-grey);
  }
  .contact__name {
    font-size: 22px; font-weight: 600;
    color: var(--brand-blue); line-height: 1.2;
  }
  .contact__title {
    font-size: 16px; color: var(--brand-red);
    line-height: 1.25; margin-bottom: 12px;
  }
  .contact__address { font-size: 16px; line-height: 23.5px; margin-bottom: 0; }
  .contact__list { list-style: none; font-size: 16px; line-height: 23.5px; }
  .contact__list li { display: flex; align-items: center; gap: 8px; }
  .contact__list svg { width: 14px; height: 14px; fill: var(--brand-blue); flex: none; }

  .front-band {
    position: absolute;
    left: 0; bottom: 0;
    width: 100%; height: 28px;
    background: linear-gradient(90deg, #0f1a8a 0%, var(--royal) 20%, #0f1a8a 32%, var(--band-silver) 42%, #f2f2f2 70%, var(--band-silver) 100%);
  }

  .back-lockup {
    position: absolute;
    left: 0; width: 100%;
    top: 112px;
    text-align: center;
    color: #ffffff;
    font-weight: 700;
  }
  .back-lockup__mark {
    width: 72px; height: 72px;
    border-radius: 50%;
    background: #ffffff;
    margin: 0 auto 18px;
  }
  .back-lockup__name { font-size: 22px; }
  .back-rule {
    position: absolute;
    left: 83px; top: 271px;
    width: 451px; height: 1px;
    background: linear-gradient(90deg, transparent, rgba(255,255,255,0.6), transparent);
  }
  .back-website {
    position: absolute;
    left: 0; width: 100%;
    top: 283px;
    text-align: center;
    color: #ffffff;
    font-size: 16px;
    letter-spacing: 2px;
  }
</style>
</head>
<body>
  <section class="card card--front" aria-label="Business card front">
    <div class="brand-lockup">
      <div class="brand-lockup__mark"></div>
      <div class="brand-lockup__name">Northline Claim Advocates</div>
    </div>
    <div class="front-divider"></div>
    <div class="contact">
      <div class="contact__name">DANIEL REYES</div>
      <div class="contact__title">CEO/Founder</div>
      <div class="contact__address">2140 Larkspur Court<br>Chicago, Illinois 60614</div>
      <ul class="contact__list">
        <li><svg viewBox="0 0 16 16"><path d="M3 1l3 3-2 2c1 2 3 4 5 5l2-2 3 3-2 3C7 15 1 9 0 3z"/></svg>312 555 0147</li>
        <li><svg viewBox="0 0 16 16"><path d="M4 0h8v16H4zM5.5 2v10h5V2zM7 13.5h2v1H7z" fill-rule="evenodd"/></svg>312 555 0189</li>
        <li><svg viewBox="0 0 16 16"><path d="M4 1h8v4H4zM1 6h14v7H1zM4 11h8v4H4z"/></svg>312 555 0162</li>
        <li><svg viewBox="0 0 16 16"><path d="M1 3h14v10H1zM2.5 4.5v.5L8 9l5.5-4v-.5zM2.5 6.8v4.7h11V6.8L8 10.8z" fill-rule="evenodd"/></svg>daniel@northlineclaims.com</li>
        <li><svg viewBox="0 0 16 16"><path d="M8 0a8 8 0 100 16A8 8 0 008 0zm-5 6c1-3 4-4 6-3-1 1-2 1-2 3s3 1 3 3-2 3-2 5C5 14 2 11 3 6z"/></svg>www.northlineclaims.com</li>
      </ul>
    </div>
    <div class="front-band"></div>
  </section>

  <section class="card card--back" aria-label="Business card back">
    <div class="back-lockup">
      <div class="back-lockup__mark"></div>
      <div class="back-lockup__name">Northline Claim Advocates</div>
    </div>
    <div class="back-rule"></div>
    <div class="back-website">www.NorthlineClaimAdvocates.com</div>
  </section>
</body>
</html>
```